LHP Regal Business Card Design 2020

Your Manor Steward is looking for a business card that is clean and straight to the point but still looks high-end and attractive. We are a team comprised of management and field professionals focused on the high-end residential marketplace. We serve homeowners and trade professionals directly based out of the Metrowest/Boston area. We provide client services as well as construction/renovation services.
We are aiming for a black and white feel (white background and black text) and a matte finish with rounded edges.

We want to emphasis our vision of "Properties - Projects - Partners".
Dana Pellham is the president of LHP

Please include the following areas we service: Boston/Cape/Newport
Please make sure to include Dana's mobile (555) 213 4480 & office number (555) 640 1937, email dana@yourmanorsteward.example and website www.yourmanorsteward.example

Colors

Designer to choose only greyscale colors for use in the design.

Requirements
Must have
• Include "Properties - Projects - Partners" in design

Include "After Hours Emergency Support # 1800 555 0142" with icon

```html
<!DOCTYPE html>
<html lang="en">
<head>
<meta charset="utf-8">
<title>LHP Business Card – Your Manor Steward</title>
<link rel="stylesheet" href="https://fonts.googleapis.com/css2?family=Raleway:wght@700&family=Roboto:wght@400;500&display=swap">
<style>
  :root {
    --page-bg: #e4e4e4;
    --card-front: #ffffff;
    --card-back: #2b2b2b;
    --ink: #222222;
    --ink-soft: #3a3a3a;
    --ink-muted: #6a6a6a;
    --mark-grey: #9c9c9c;
    --area-text: #f2f2f2;
  }
  * { margin: 0; padding: 0; box-sizing: border-box; }
  html, body { width: 1173px; height: 1200px; overflow: hidden; }
  body { background: var(--page-bg); position: relative; font-family: "Roboto", sans-serif; }

  .card { position: absolute; width: 742px; height: 411px; }
  .card-front { left: 205px; top: 150px; background: var(--card-front); }
  .card-back { left: 204px; top: 636px; background: var(--card-back); }

  .holder { position: absolute; left: 61px; top: 88px; }
  .holder-name {
    font-family: "Raleway", sans-serif; font-weight: 700; font-size: 26px;
    color: var(--ink); letter-spacing: -0.2px; line-height: 1;
  }
  .holder-title { font-size: 20px; font-weight: 500; color: var(--ink-soft); margin-top: 6px; }
  .vision {
    font-size: 15px; color: var(--ink-muted); margin-top: 18px;
    letter-spacing: 0.5px; white-space: nowrap;
  }

  .brand { position: absolute; text-align: center; }
  .brand-initials {
    font-family: "Raleway", sans-serif; font-weight: 700; line-height: 1;
    letter-spacing: 2px;
  }
  .brand-name {
    font-family: "Raleway", sans-serif; font-weight: 700; letter-spacing: 2.5px;
    white-space: nowrap;
  }
  .card-front .brand { left: 378px; top: 46px; width: 268px; }
  .card-front .brand-initials { font-size: 110px; color: var(--ink); }
  .card-front .brand-name { font-size: 16px; color: var(--ink); margin-top: 12px; }

  .card-back .brand { left: 0; top: 104px; width: 100%; }
  .card-back .brand-initials { font-size: 150px; color: var(--mark-grey); }
  .card-back .brand-name { font-size: 22px; color: var(--mark-grey); margin-top: 14px; letter-spacing: 3.5px; }

  .contacts { position: absolute; left: 378px; top: 258px; list-style: none; }
  .contacts li {
    display: flex; align-items: center; height: 25px;
    font-size: 19px; color: var(--ink-soft);
  }
  .contacts svg { width: 16px; height: 16px; margin-right: 10px; flex: none; fill: var(--ink); }

  .emergency {
    position: absolute; left: 61px; top: 374px;
    display: flex; align-items: center;
    font-size: 14px; color: var(--ink-soft); white-space: nowrap;
  }
  .emergency svg { width: 14px; height: 14px; margin-right: 8px; fill: var(--ink); flex: none; }

  .service-areas {
    position: absolute; left: 0; top: 358px; width: 100%; text-align: center;
    font-size: 18px; color: var(--area-text); word-spacing: 1px;
  }
</style>
</head>
<body>

<section class="card card-front">
  <div class="holder">
    <p class="holder-name">DANA PELLHAM</p>
    <p class="holder-title">President</p>
    <p class="vision">Properties - Projects - Partners</p>
  </div>

  <div class="brand">
    <p class="brand-initials">LHP</p>
    <p class="brand-name">YOUR MANOR STEWARD</p>
  </div>

  <ul class="contacts">
    <li>
      <svg viewBox="0 0 16 16" aria-hidden="true"><path d="M4 0h8a1.5 1.5 0 0 1 1.5 1.5v13A1.5 1.5 0 0 1 12 16H4a1.5 1.5 0 0 1-1.5-1.5v-13A1.5 1.5 0 0 1 4 0zm0.2 2v10.5h7.6V2zM8 13.3a0.9 0.9 0 1 0 0 1.8 0.9 0.9 0 0 0 0-1.8z"/></svg>
      (555) 213 4480
    </li>
    <li>
      <svg viewBox="0 0 16 16" aria-hidden="true"><path d="M1 5c0-2 3-3 7-3s7 1 7 3v1.5h-3.5V5h-7v1.5H1zM4 7.5h8l2 3v4H2v-4zm4 1.5a2 2 0 1 0 0 4 2 2 0 0 0 0-4z"/></svg>
      (555) 640 1937
    </li>
    <li>
      <svg viewBox="0 0 16 16" aria-hidden="true"><path d="M0 3h16v10H0zm1.6 1.2L8 9l6.4-4.8v-0.1H1.6zm-0.5 1.3v6.3l4.2-3.1zm13.8 0l-4.2 3.2 4.2 3.1zM6.2 8.4L1.6 11.9h12.8L9.8 8.4 8 9.8z"/></svg>
      dana@yourmanorsteward.example
    </li>
    <li>
      <svg viewBox="0 0 16 16" aria-hidden="true"><path d="M8 0a8 8 0 1 1 0 16A8 8 0 0 1 8 0zm-2 2.2a6 6 0 0 0-3.8 7.2l1.8-0.6 1 1.6-0.6 2.2a6 6 0 0 0 2 1.1l0.8-2.6 1.8-1-0.6-2.2-2.4-0.4-0.2-1.6 1.6-1.2zm4.5 0.4l-0.7 1.6 1.4 1.2 2.2-0.2a6 6 0 0 0-2.9-2.6z"/></svg>
      www.yourmanorsteward.example
    </li>
  </ul>

  <p class="emergency">
    <svg viewBox="0 0 16 16" aria-hidden="true"><path d="M8 0.5 15.5 15H0.5zM7 6v4.5h2V6zm0 6v1.8h2V12z"/></svg>
    After Hours Emergency Support # 1800 555 0142
  </p>
</section>

<section class="card card-back">
  <div class="brand">
    <p class="brand-initials">LHP</p>
    <p class="brand-name">YOUR MANOR STEWARD</p>
  </div>
  <p class="service-areas">● Boston ● Metrowest ● South Shore ● Cape ● Newport</p>
</section>

</body>
</html>
```